Automotive component supplier needs a business card design

We need a business card design for our company called Velran Global Components Ltd based in the UK. We are a supplier of interior and exterior components to premium car manufacturers such as Corvel Ashby, Hadley Fenn, Marquist and Tavarelli. We would like to see a modern business card design that uses the colour blue.

Target Market(s)

Premium automotive car manufacturers.

Industry/Entity Type

Automotive

Contact Information for Business Card

Company Name : Velran Global Components Limited
Address: 17 Marlow Yard, Upper Heath, Warwick, CV31 8QL, United Kingdom
Web Address : www.velrancomponents-example.co.uk

Font styles to use
Other font styles liked:
• Helvetica

Colors
3176b5
0255a3
85acd3
cfdeed
cee9f5
85cae6
34a6d7
0692cd
9bcb3c

Requirements
Must have
• Clear company logo and a mixture of blue colours.
Nice to have
• A high quality modern image.
Should not have
• Multiple colours.

```html
<!DOCTYPE html>
<html lang="en">
<head>
<meta charset="utf-8">
<title>Velran Global Components – Business Card</title>
<link rel="stylesheet" href="https://fonts.googleapis.com/css2?family=Source+Sans+3:wght@400;600;700&display=swap">
<style>
  :root {
    --blue: #0692cd;
    --blue-deep: #0a84c6;
    --green: #9bcb3c;
    --ink: #3d3d3d;
    --paper: #ffffff;
    --backdrop: #e9ecef;
  }
  html, body {
    margin: 0;
    width: 1200px;
    height: 987px;
    overflow: hidden;
    background: var(--backdrop);
    font-family: "Source Sans 3", Helvetica, Arial, sans-serif;
  }
  .canvas { position: relative; width: 1200px; height: 987px; }
  .card {
    position: absolute;
    left: 292px;
    width: 616px;
    height: 340px;
    box-shadow: 0 3px 10px rgba(0,0,0,0.25);
    overflow: hidden;
  }
  .card-front { top: 128px; background: var(--paper); }
  .card-back { top: 508px; background: var(--blue); }

  .brand {
    position: absolute;
    font-weight: 700;
    text-transform: uppercase;
    letter-spacing: 0.5px;
    line-height: 1.05;
  }
  .card-front .brand {
    right: 36px; top: 40px;
    text-align: right;
    color: var(--blue);
    font-size: 30px;
  }
  .card-back .brand {
    left: 0; right: 0; top: 118px;
    text-align: center;
    color: var(--paper);
    font-size: 44px;
  }

  .person { position: absolute; left: 35px; top: 134px; }
  .person-name { margin: 0; font-size: 22px; font-weight: 600; color: var(--blue); }
  .person-role { margin: 2px 0 0; font-size: 16px; color: var(--green); }

  .divider {
    position: absolute; left: 35px; right: 36px; top: 208px;
    height: 1.5px; background: var(--blue);
  }

  .contacts {
    position: absolute; left: 35px; top: 219px;
    margin: 0; padding: 0; list-style: none;
    font-size: 16px; color: var(--ink);
  }
  .contacts li { display: flex; align-items: center; height: 23.4px; }
  .contacts svg { width: 15px; height: 15px; margin-right: 7px; fill: var(--blue); }

  .address {
    position: absolute; right: 36px; top: 246px;
    margin: 0; font-style: normal; text-align: right;
    font-size: 16px; line-height: 21.5px; color: var(--ink);
  }

  .stripe-green { position: absolute; left: 0; right: 0; bottom: 11px; height: 2px; background: var(--green); }
  .stripe-blue { position: absolute; left: 0; right: 0; bottom: 0; height: 9px; background: var(--blue); }

  .web {
    position: absolute; left: 0; right: 0; top: 290px;
    text-align: center; color: var(--paper);
    font-size: 15px; letter-spacing: 5px;
  }
</style>
</head>
<body>
<div class="canvas">
  <section class="card card-front">
    <div class="brand">Velran<br>Global Components</div>

    <div class="person">
      <p class="person-name">Elliot Marsh</p>
      <p class="person-role">CEO/Founder</p>
    </div>

    <div class="divider"></div>

    <ul class="contacts">
      <li><svg viewBox="0 0 16 16"><path d="M3.5 1.5l2.5 0 1.2 3.2-1.7 1.3c.8 1.8 2.2 3.2 4 4l1.3-1.7 3.2 1.2v2.5c0 .8-.7 1.5-1.5 1.5C6.9 13.5 2 8.6 2 3c0-.8.7-1.5 1.5-1.5z"/></svg>689 512 7740</li>
      <li><svg viewBox="0 0 16 16"><path d="M4.5 0.5h7c.6 0 1 .4 1 1v13c0 .6-.4 1-1 1h-7c-.6 0-1-.4-1-1v-13c0-.6.4-1 1-1zm.8 2v9.5h5.4V2.5zM8 12.8a.9.9 0 1 0 0 1.8.9.9 0 0 0 0-1.8z"/></svg>836 204 5187</li>
      <li><svg viewBox="0 0 16 16"><path d="M1 3.5h14v9H1zM2.2 4.5L8 9l5.8-4.5z" fill-rule="evenodd"/></svg>elliot@velrancomponents-example.co.uk</li>
      <li><svg viewBox="0 0 16 16"><path d="M8 1a7 7 0 1 0 0 14A7 7 0 0 0 8 1zm0 1.5c.9 0 1.9 1.9 2.1 4.7H5.9C6.1 4.4 7.1 2.5 8 2.5zM5.9 8.8h4.2c-.2 2.8-1.2 4.7-2.1 4.7s-1.9-1.9-2.1-4.7zM2.6 7.2a5.5 5.5 0 0 1 2.6-4c-.4 1-.7 2.4-.8 4zm0 1.6h1.8c.1 1.6.4 3 .8 4a5.5 5.5 0 0 1-2.6-4zm10.8 0a5.5 5.5 0 0 1-2.6 4c.4-1 .7-2.4.8-4zm0-1.6h-1.8c-.1-1.6-.4-3-.8-4a5.5 5.5 0 0 1 2.6 4z"/></svg>www.velrancomponents-example.co.uk</li>
    </ul>

    <address class="address">17 Marlow Yard, Upper Heath<br>Warwick, CV31 8QL<br>United Kingdom</address>

    <div class="stripe-green"></div>
    <div class="stripe-blue"></div>
  </section>

  <section class="card card-back">
    <div class="brand">Velran<br>Global Components</div>
    <div class="web">www.velrancomponents-example.co.uk</div>
  </section>
</div>
</body>
</html>
```